freshen up existing wordpress site

We wish to re-implement our current wordpress website www.vornimax.com/web2.

The content, structure and menus of the website should remain the same, but style updated to a more fresh/contemporary layout. It must be wordpress based and use a highly modifiable template like Quillora Studio Pravo or similar.

Permalinks must be exactly as the old ones.

Landing page must contain a slider for images and movies, plus a little text. There is no requirement for a tab-style as seem on the current website.

The final result shall be transferred to a fresh multisite installation of wordpress, we will provide login for access later. If another method is better/more preferred, please comment and we can take it from there.

The two graphics on http://vornimax.com/web2/gridmarshal-product-details/ should be re-done to look more 'clean and professional' and look less powerpoint'ish. We will need the vectorfiles for edits later on. Color scheme is open, whatever matches with the the website style.

We work in a engineering-heavy B2B environment, so slightly conservative/boring styles; no 'pop smartness'. competitors websites looks like this:
- http://www.lumivex.com/
- http://www.corbantix.com/
- https://www.ostrivel.com/products/ic_nanometer_design/
- https://www.quendor-da.com/

Website background should be white for easy image implementation. Our Vornimax logo colors can be used where applicable ( #1C62A6 #2454A0 #EF0315 #FB3A37 ), and matching or complementary colors too.

Use Sans Serif fonts like googles or something like http://www.glyphbarrow.com/fonts/noto-sans .

Target Market(s)

semiconductor industry

Number of Pages Required

5+ page

Font styles to use
Sans Serif

Requirements
Must have
• see above
Nice to have
• see above
Should not have
• not defined.

```html
<!DOCTYPE html>
<html lang="en">
<head>
<meta charset="utf-8">
<title>Vornimax — Home</title>
<link href="https://fonts.googleapis.com/css2?family=Ubuntu:wght@400;500;700&family=Lato:wght@400;700&family=Crimson+Text:wght@700&display=swap" rel="stylesheet">
<style>
:root{
  --navy:#0d1f5c;
  --navy-deep:#0a1a4f;
  --blue:#1c62a6;
  --red:#ef0315;
  --red-soft:#fb3a37;
  --ink:#1f1f1f;
  --muted:#e6e6e6;
  --page:#f7f7f7;
  --white:#ffffff;
}
*{box-sizing:border-box;margin:0;padding:0}
html,body{width:965px;height:1200px;overflow:hidden;background:var(--white)}
body{position:relative;font-family:"Lato",sans-serif;color:var(--ink)}
.abs{position:absolute}

/* top bar + header */
.top-line{left:0;top:0;width:965px;height:4px;background:var(--navy)}
.header{left:0;top:0;width:965px;height:96px;background:linear-gradient(#fff,#f4f4f4);border-bottom:1px solid #ddd}
.top-email{left:599px;top:7px;font-size:12px;color:#333;display:flex;align-items:center;gap:6px}
.top-phone{left:745px;top:0;width:138px;height:27px;background:var(--navy);border-radius:0 0 18px 18px;color:#fff;font-family:"Ubuntu",sans-serif;font-size:14px;font-weight:500;display:flex;align-items:center;justify-content:center;gap:6px}
.logo{left:65px;top:42px;display:flex;align-items:center;gap:6px;font-family:"Ubuntu",sans-serif;font-weight:700;font-size:36px;color:var(--navy);letter-spacing:-1px;line-height:1}
.logo-mark{width:30px;height:30px;background:var(--blue)}
.nav{left:410px;top:58px;display:flex;align-items:center;font-family:"Ubuntu",sans-serif;font-weight:500;font-size:15px;color:#222}
.nav a{color:inherit;text-decoration:none;padding:0 16px;border-left:1px solid #ddd;line-height:18px}
.nav a:first-child{border-left:none;padding-left:2px;padding-right:12px}

/* slider */
.slider{left:0;top:96px;width:965px;height:330px;background:radial-gradient(ellipse at 30% 50%,#9ec9d2 0%,#4f97a9 40%,#1f5f77 100%)}
.slide-caption{left:600px;top:198px;width:300px;height:128px;background:rgba(30,70,90,.45);padding:18px 6px 0 0;text-align:right;font-family:"Crimson Text",serif;font-weight:700;font-size:24px;line-height:30px;color:#fff}
.slide-arrow{top:230px;width:28px;height:28px;background:#333;display:flex;align-items:center;justify-content:center}
.slide-arrow.prev{left:5px}.slide-arrow.next{left:928px}
.slider-base{left:0;top:424px;width:965px;height:3px;background:#bbb}

/* about product */
.about{left:0;top:427px;width:965px;height:542px;background:var(--page)}
.section-title{left:0;top:448px;width:965px;text-align:center;font-family:"Ubuntu",sans-serif;font-size:24px;color:var(--navy)}
.section-title em,.block-title em{font-style:normal;color:var(--red)}
.title-rule{left:342px;top:490px;width:280px;height:1px;background:#bbb}
.title-dot{left:475px;top:483px;width:14px;height:14px;background:var(--red)}
.product-frame{left:64px;top:517px;width:328px;height:206px;background:#fff;border:1px solid #ddd;padding:8px}
.product-image{width:100%;height:100%;background:linear-gradient(#2f8f3a,#7ec23e 45%,#d86a1c 75%,#c23410)}
.product-name{left:419px;top:525px;font-family:"Ubuntu",sans-serif;font-size:22px;color:var(--red)}
.product-sub{left:419px;top:551px;font-family:"Ubuntu",sans-serif;font-size:17px;color:var(--navy)}
.product-text{left:420px;top:579px;width:475px;font-size:12px;line-height:17px}
.btn{top:679px;width:144px;height:34px;background:var(--navy);color:#fff;font-family:"Ubuntu",sans-serif;font-weight:700;font-size:14px;display:flex;align-items:center;justify-content:center}

/* welcome */
.block-title{font-family:"Ubuntu",sans-serif;font-size:23px;color:var(--navy)}
.welcome-icon{left:64px;top:757px;width:28px;height:28px;background:var(--blue)}
.welcome-title{left:104px;top:756px}
.welcome-rule{left:64px;top:793px;width:514px;height:1px;background:#ccc}
.welcome-text{left:70px;top:804px;width:515px;font-size:12px;line-height:17px}
.checks{left:70px;top:862px;list-style:none;font-size:12px;line-height:22px}
.checks li{display:flex;align-items:center;gap:6px}
.col-divider{left:606px;top:760px;width:1px;height:205px;background:linear-gradient(#fff,#ddd,#fff)}

/* news */
.news-title{left:630px;top:756px;display:flex;align-items:center;gap:8px}
.news-nav{left:881px;top:766px;font-size:12px;color:#444}
.news-rule{left:630px;top:793px;width:270px;height:1px;background:#ccc}
.news-item{left:630px;width:270px;height:62px;display:flex;gap:7px;border-bottom:1px solid #eee}
.news-date{width:37px;height:47px;background:var(--navy);color:#fff;text-align:center;font-family:"Ubuntu",sans-serif}
.news-date b{display:block;font-weight:400;font-size:17px;line-height:28px}
.news-date span{display:block;background:var(--navy-deep);font-size:11px;line-height:19px;font-weight:500}
.news-body h4{font-size:11px;font-weight:700;line-height:16px}
.news-body p{font-size:10.5px;line-height:13px}

/* footer */
.footer{left:0;top:969px;width:965px;height:195px;background:var(--navy)}
.foot-head{top:990px;font-family:"Ubuntu",sans-serif;font-size:15px;color:#fff;padding-bottom:9px;border-bottom:1px dashed #4b5d99}
.quick-links{left:66px;top:1027px;list-style:none;font-size:11px;line-height:19.3px;color:#fff}
.quick-links li::before{content:"›";color:var(--red);margin-right:8px}
.field{left:244px;width:180px;background:#fff;border:1px solid #ccc;font-size:9px;color:#555;padding:3px 6px}
.submit{left:245px;top:1118px;width:52px;height:19px;background:var(--red);color:#fff;font-size:11px;font-weight:700;display:flex;align-items:center;justify-content:center}
.contact-row{left:502px;width:190px;display:flex;gap:8px;font-size:11px;line-height:14px;color:#fff;border-bottom:1px solid #2a3c7a;padding-bottom:8px}
.foot-logo{left:760px;top:1060px;width:140px;text-align:center;font-family:"Ubuntu",sans-serif;font-weight:700;font-size:30px;color:#d9d9d9;letter-spacing:-1px}
.foot-mark{left:817px;top:1032px;width:26px;height:26px;background:#d9d9d9}
.social{top:1111px;width:26px;height:26px;border-radius:50%;background:var(--red)}
.copyright{left:0;top:1164px;width:965px;height:36px;background:var(--red);color:#fff;font-size:11px;font-weight:700;display:flex;align-items:center;justify-content:center}
</style>
</head>
<body>

<div class="abs header"></div>
<div class="abs top-line"></div>
<div class="abs top-email">
  <svg width="14" height="10" viewBox="0 0 14 10"><rect width="14" height="10" fill="#333"/><path d="M0 0l7 6 7-6" stroke="#fff" fill="none"/></svg>
  info@vornimax.com
</div>
<div class="abs top-phone">
  <svg width="11" height="12" viewBox="0 0 11 12"><path d="M2 0l2 3-1 2c1 2 2 3 4 4l1-1 3 2-1 2C5 12 0 7 0 2z" fill="#fff"/></svg>
  555-014-2290
</div>
<div class="abs logo"><span class="logo-mark"></span>vornimax</div>
<nav class="abs nav">
  <a href="#"><svg width="22" height="20" viewBox="0 0 22 20"><path d="M11 1L1 10h3v9h5v-6h4v6h5v-9h3z" fill="#ef0315"/></svg></a>
  <a href="#">About Us</a><a href="#">Products</a><a href="#">Company</a><a href="#">News</a><a href="#">Contact Us</a>
</nav>

<div class="abs slider" role="img" aria-label="Photo of a hand touching a glowing circuit board in blue tones"></div>
<div class="abs slide-caption">High-Performance Interface Enables Early and Accurate Power Profiling of Real-Time Applications</div>
<div class="abs slide-arrow prev"><svg width="8" height="12" viewBox="0 0 8 12"><path d="M7 1L2 6l5 5" stroke="#fff" stroke-width="2" fill="none"/></svg></div>
<div class="abs slide-arrow next"><svg width="8" height="12" viewBox="0 0 8 12"><path d="M1 1l5 5-5 5" stroke="#fff" stroke-width="2" fill="none"/></svg></div>
<div class="abs slider-base"></div>

<section class="abs about"></section>
<h2 class="abs section-title">About <em>Our</em> Product</h2>
<div class="abs title-rule"></div>
<div class="abs title-dot"></div>
<div class="abs product-frame"><div class="product-image" role="img" aria-label="Close-up of a chip wafer glowing green to red"></div></div>
<h3 class="abs product-name">GridMarshal 4</h3>
<p class="abs product-sub">Reducing Dynamic Voltage Drop &amp; In-rush Current</p>
<p class="abs product-text">Lorem ipsum dolor sit amet, consectetuer adipiscing elit, sed diam nonummy nibh euismod tincidunt ut laoreet dolore magna aliquam erat volutpat. Ut wisi enim ad minim veniam, quis nostrud exerci tation ullamcorper suscipit lobortis nisl ut aliquip ex ea commodo consequat.ipsum dolor sit amet, consectetuer adipiscing elit, sed diam nonummy nibh euismod tincidunt ut laoreet dolore magna aliquam erat volutpat.</p>
<div class="abs btn" style="left:422px">Advantages</div>
<div class="abs btn" style="left:577px">Product Details</div>

<div class="abs welcome-icon"></div>
<h2 class="abs block-title welcome-title"><em>Welcome to</em> Vornimax</h2>
<div class="abs welcome-rule"></div>
<p class="abs welcome-text">Lorem ipsum dolor sit amet, consectetuer adipiscing elit, sed diam nonummy nibh euismod tincidunt ut laoreet dolore magna aliquam erat volutpat. Ut wisi enim ad minim veniam, quis nostrud exerci tation ullamcorper suscipit lobortis nisl ut aliquip ex ea commodo consequat.</p>
<ul class="abs checks">
  <li><svg width="11" height="10" viewBox="0 0 11 10"><path d="M1 5l3 4 6-8" stroke="#ef0315" stroke-width="2" fill="none"/></svg>Lorem ipsum dolor sit amet, consectetuer adipiscing elit</li>
  <li><svg width="11" height="10" viewBox="0 0 11 10"><path d="M1 5l3 4 6-8" stroke="#ef0315" stroke-width="2" fill="none"/></svg>Lorem ipsum dolor sit amet consectetuer</li>
  <li><svg width="11" height="10" viewBox="0 0 11 10"><path d="M1 5l3 4 6-8" stroke="#ef0315" stroke-width="2" fill="none"/></svg>Lorem ipsum dolor sit amet consectetuer adipiscing</li>
</ul>
<div class="abs col-divider"></div>

<h2 class="abs block-title news-title">
  <svg width="24" height="22" viewBox="0 0 24 22"><path d="M1 8h5l12-7v20L6 14H1z" fill="#ef0315"/><path d="M4 14l2 7h3l-2-7z" fill="#ef0315"/><rect x="19" y="5" width="4" height="12" fill="#0d1f5c"/></svg>
  <span><em>Latest</em> News</span>
</h2>
<div class="abs news-nav">‹ ›</div>
<div class="abs news-rule"></div>
<article class="abs news-item" style="top:808px">
  <div class="news-date"><b>23</b><span>Jan</span></div>
  <div class="news-body"><h4>Duis autem vel eum iriure</h4><p>Lorem ipsum dolor sit amet, in the adipiscing magnagt Lorem ipsum dolor...</p></div>
</article>
<article class="abs news-item" style="top:877px">
  <div class="news-date"><b>23</b><span>Jan</span></div>
  <div class="news-body"><h4>Duis autem vel eum iriure</h4><p>Lorem ipsum dolor sit amet, in the adipiscing magnagt Lorem ipsum dolor...</p></div>
</article>

<footer class="abs footer"></footer>
<h3 class="abs foot-head" style="left:66px;width:100px">Quick Links</h3>
<ul class="abs quick-links">
  <li>Home</li><li>About Us</li><li>Products</li><li>Company</li><li>News</li><li>Contact Us</li>
</ul>
<h3 class="abs foot-head" style="left:243px;width:182px">Quick Inquiry</h3>
<div class="abs field" style="top:1031px;height:18px">Name</div>
<div class="abs field" style="top:1055px;height:18px">Email</div>
<div class="abs field" style="top:1078px;height:33px">Message</div>
<div class="abs submit">Submit</div>
<h3 class="abs foot-head" style="left:502px;width:190px">Contact Details</h3>
<div class="abs contact-row" style="top:1029px">
  <svg width="10" height="13" viewBox="0 0 10 13"><path d="M5 0a5 5 0 0 1 5 5c0 3-5 8-5 8S0 8 0 5a5 5 0 0 1 5-5z" fill="#ef0315"/><circle cx="5" cy="5" r="2" fill="#0d1f5c"/></svg>
  <span>123 euismod cidun ut laoreetmok laoreet dol magnak aliquam PG Feugait.</span>
</div>
<div class="abs contact-row" style="top:1088px;font-size:12px">
  <svg width="11" height="12" viewBox="0 0 11 12"><path d="M2 0l2 3-1 2c1 2 2 3 4 4l1-1 3 2-1 2C5 12 0 7 0 2z" fill="#ef0315"/></svg>
  <span>555 - 014 - 2290</span>
</div>
<div class="abs contact-row" style="top:1121px;border:none;font-size:12px">
  <svg width="12" height="9" viewBox="0 0 12 9"><rect width="12" height="9" fill="#ef0315"/><path d="M0 0l6 5 6-5" stroke="#0d1f5c" fill="none"/></svg>
  <span>info@vornimax.com</span>
</div>
<div class="abs foot-mark"></div>
<div class="abs foot-logo">vornimax</div>
<div class="abs social" style="left:764px" aria-label="Social link"></div>
<div class="abs social" style="left:800px" aria-label="Social link"></div>
<div class="abs social" style="left:835px" aria-label="Social link"></div>
<div class="abs social" style="left:870px" aria-label="Social link"></div>
<div class="abs copyright">Copyright © 2016 Vornimax. All Right Reserved.</div>

</body>
</html>
```